Brightfen Business Card Redesign & Logo Update

We need to update our business cards to something more modern and fresh. Brightfen can provide the current color schemes and old design examples, but welcome creativity in helping us with this redesign. PLEASE NOTE that we no longer utilize the "tree" and/or "leaf" imagery in our branding. If able would apprecaite an update on the quality of our "words only" logo in Ai. / PNG formats too.

Target Market(s)

Investors, landowners, corporate partners, contractors

Industry/Entity Type

Environmental Restoration & Conservation

Contact Information for Business Card

Logo, persons name, title, mailing address, phone and email, website url

Font styles to use
Other font styles liked:
• Merriweather

Requirements
Nice to have
• Logo, persons name, title, mailing address, phone and email, website url, but open to ideams
Should not have
• No all back backgrounds

```html
<!DOCTYPE html>
<html lang="en">
<head>
<meta charset="utf-8">
<title>Brightfen Business Card</title>
<link rel="stylesheet" href="https://fonts.googleapis.com/css2?family=Merriweather:wght@400;700;900&display=swap">
<style>
  :root {
    --backdrop: #9b9b9b;
    --card: #ffffff;
    --orange: #ec7a23;
    --green: #167a3c;
    --ink: #111111;
    --text: #3a3a3a;
  }
  * { margin: 0; padding: 0; box-sizing: border-box; }
  html, body {
    width: 1049px; height: 1200px; overflow: hidden;
    background: var(--backdrop);
    font-family: "Merriweather", Georgia, serif;
  }
  .card {
    position: absolute; left: 164px; width: 723px; height: 413px;
    background: var(--card); border-radius: 26px; overflow: hidden;
  }
  .card--front { top: 140px; }
  .card--back { top: 646px; }

  .wordmark { position: absolute; text-align: center; }
  .wordmark__name { color: var(--green); font-weight: 900; letter-spacing: 0.01em; line-height: 1; display: block; }
  .wordmark__tagline { color: var(--ink); font-weight: 700; display: block; letter-spacing: 0.01em; }

  .card--front .wordmark { left: 0; right: 0; top: 150px; }
  .card--front .wordmark__name { font-size: 62px; }
  .card--front .wordmark__tagline { font-size: 20px; margin-top: 14px; }

  .card--back .wordmark { left: 38px; top: 50px; width: 268px; }
  .card--back .wordmark__name { font-size: 37px; }
  .card--back .wordmark__tagline { font-size: 12.4px; margin-top: 9px; }

  .address { position: absolute; left: 38px; top: 178px; font-size: 19.5px; line-height: 29px; color: var(--text); }

  .contacts { position: absolute; left: 38px; top: 286px; list-style: none; font-size: 19.5px; line-height: 29px; color: var(--text); }
  .contacts li { display: flex; align-items: center; gap: 8px; }
  .contacts svg { width: 16px; height: 16px; flex: none; margin-top: 5px; }

  .person { position: absolute; right: 43px; top: 178px; text-align: right; }
  .person__name { font-size: 27.5px; font-weight: 700; color: var(--green); line-height: 1.2; }
  .person__title { font-size: 20px; color: var(--orange); line-height: 1.3; }

  .edge-band { position: absolute; right: 0; width: 17px; }
  .edge-band--top { top: 0; height: 177px; background: var(--green); border-bottom-left-radius: 6px; }
  .edge-band--mid { top: 184px; height: 46px; background: var(--orange); border-radius: 6px 0 0 6px; }
  .edge-band--bottom { top: 236px; bottom: 0; background: var(--green); border-top-left-radius: 6px; }
</style>
</head>
<body>
  <section class="card card--front">
    <div class="wordmark">
      <span class="wordmark__name">BRIGHTFEN</span>
      <span class="wordmark__tagline">ENVIRONMENTAL CREDIT COMPANY</span>
    </div>
  </section>

  <section class="card card--back">
    <div class="wordmark">
      <span class="wordmark__name">BRIGHTFEN</span>
      <span class="wordmark__tagline">ENVIRONMENTAL CREDIT COMPANY</span>
    </div>

    <p class="address">18340 Harbor Crest Dr<br>Calder Bay CA 90412</p>

    <ul class="contacts">
      <li>
        <svg viewBox="0 0 16 16" aria-hidden="true"><path fill="#ec7a23" d="M3.2 1.5l2.4 2.6-1.3 1.8c.9 2.2 2.6 3.9 4.8 4.8l1.8-1.3 2.6 2.4-1.6 2.3C6.7 13.6 2.4 9.3 1 4.1z"/></svg>
        555-014-2287
      </li>
      <li>
        <svg viewBox="0 0 16 16" aria-hidden="true"><rect x="1" y="4" width="14" height="9" rx="1.5" fill="#ec7a23"/><path d="M1.5 5l6.5 4.5L14.5 5" fill="none" stroke="#fff" stroke-width="1.3"/></svg>
        dkirwell@brightfen.com
      </li>
      <li>
        <svg viewBox="0 0 16 16" aria-hidden="true"><circle cx="8" cy="8" r="7" fill="#ec7a23"/><path d="M1 8h14M8 1c-3 3.5-3 10.5 0 14M8 1c3 3.5 3 10.5 0 14" fill="none" stroke="#fff" stroke-width="1.1"/></svg>
        www.brightfen.com
      </li>
    </ul>

    <div class="person">
      <p class="person__name">DANA KIRWELL</p>
      <p class="person__title">President</p>
    </div>

    <div class="edge-band edge-band--top"></div>
    <div class="edge-band edge-band--mid"></div>
    <div class="edge-band edge-band--bottom"></div>
  </section>
</body>
</html>
```